Webdesign für HALDEN STAHLWERK
Zielgruppe
Valkorin ist Ihr leistungsstarker und zuverlässiger Partner im Bereich Metallverarbeitung. Seit unserer Firmengründung im Jahr 2001 ist unser inhabergeführtes Unternehmen in Kellbach bei Auenstadt kontinuierlich gewachsen und beschäftigt derzeit 20 engagierte und qualifizierte Mitarbeiter.
Mit der Einweihung unserer neuen Fertigungshalle 2010 haben wir unsere Produktionsfläche auf 1.400 m2 vergrößert und können Ihnen nun einen noch umfassenderen Service anbieten.
Von der CNC-gesteuerten Teilefertigung bis zu modernsten Schweiß-, Schneid-, und Bearbeitungsanlagen – für die Realisierung Ihrer individuellen Wünsche steht uns ein innovativer Maschinenpark zur Verfügung. Wir fertigen zuverlässig und termingerecht nach Ihren Plänen oder übernehmen bei Bedarf auch die gesamte Abwicklung Ihres Projektes – alles made in germany!
Das Unternehmen spricht ausschließlich B2B Kunden an.
Die Hauptleistungsbereiche sind:
- Stahl- und Palettenbau
- Blechbearbeitung
- Edelstahlbearbeitung
- Mechanische Fertigung
Aufgabenstellung
- Mitlaufende Kontaktleiste
- Integration der Social Media Kanäle
- Sehr modernes Auftreten
- Industrielles Design
- Verlinkung zum Partnerunternehmen https://www.valkorin-beispiel.de/ias/index.html

```html
<!DOCTYPE html>
<html lang="de">
<head>
<meta charset="utf-8">
<title>Halden Stahlwerk – Valkorin</title>
<link href="https://fonts.googleapis.com/css2?family=Space+Grotesk:wght@400;500;600;700&display=swap" rel="stylesheet">
<style>
:root{
  --backdrop:#e1e5e9;
  --page:#ffffff;
  --band:#f4f4f4;
  --ink:#2b2a1e;
  --muted:#5c5c55;
  --navy:#0c3a72;
  --star:#1b4b86;
  --field:#f1f1f1;
}
*{box-sizing:border-box;margin:0;padding:0}
html,body{width:1200px;height:3951px;overflow:hidden}
body{background:var(--backdrop);font-family:"Space Grotesk",sans-serif;color:var(--ink);position:relative}
.page{position:absolute;left:109px;top:109px;width:982px;height:3736px;background:var(--page);overflow:hidden}
.abs{position:absolute}
.nav{left:46px;top:38px;display:flex;align-items:center;gap:22px;font-size:14px;font-weight:500}
.logo{font-weight:700;letter-spacing:-1px;color:var(--ink)}
.header-logo{left:0;width:100%;top:26px;text-align:center;font-size:28px}
.header-icons{right:46px;top:34px;display:flex;gap:20px}
.hero{left:0;top:89px;width:982px;height:427px;background:linear-gradient(110deg,#232323 0%,#3a3c40 45%,#5b6f8c 70%,#2e3a52 100%)}
.hero-kicker{left:84px;top:207px;color:#fff;font-size:16px;font-weight:500}
.hero-title{left:84px;top:244px;color:#fff;font-size:41px;font-weight:500;line-height:41px}
.product-band{left:0;top:516px;width:982px;height:281px;background:var(--band)}
.side-label{font-size:14px;font-weight:700;transform:rotate(-90deg);transform-origin:left top}
.product{top:450px;width:243px;height:344px;background:#fff;box-shadow:0 2px 10px rgba(0,0,0,.12);text-align:center}
.product .img{margin:42px auto 0;width:180px;height:165px;background:linear-gradient(180deg,#5c9a8e,#2f7669);border-radius:2px}
.product h3{font-size:14px;font-weight:700;margin-top:46px}
.product p{font-size:14px;line-height:21px;color:var(--muted);margin-top:6px}
.btn{display:inline-block;background:var(--navy);color:#fff;font-size:14px;font-weight:600;letter-spacing:.6px;text-align:center}
.feat-img{width:514px;height:261px}
.feat-text{width:320px}
.feat-text h2{font-size:17px;font-weight:600}
.feat-text p{font-size:14px;line-height:21px;color:var(--muted);margin-top:18px}
.link{display:inline-block;margin-top:20px;font-size:14px;font-weight:700;color:var(--navy);letter-spacing:.8px;border-bottom:2px solid var(--navy);padding-bottom:3px}
.right{text-align:right}
.reviews{left:0;top:2313px;width:982px;height:284px;background:var(--band)}
.review{top:2342px;width:238px;height:224px;background:#fff;box-shadow:0 2px 10px rgba(0,0,0,.1);text-align:center;padding:22px 14px 0}
.review h3{font-size:14px;font-weight:700;margin-top:10px;line-height:20px}
.review p{font-size:14px;line-height:21px;color:var(--muted);margin-top:6px}
.review small{display:block;font-size:10px;line-height:12px;color:var(--muted);margin-top:8px}
.about-title{left:0;width:982px;top:2634px;text-align:center;font-size:24px;font-weight:500}
.about-img{top:2697px;width:294px;height:161px}
.about-col{top:2890px;width:240px}
.about-col h3{font-size:24px;font-weight:500}
.about-col p{font-size:14px;line-height:21px;color:var(--muted);margin-top:16px}
.contact{left:150px;top:3127px;width:682px;height:246px;background:#fff;box-shadow:0 3px 14px rgba(0,0,0,.12);padding:34px 36px}
.contact h2{text-align:center;font-size:22px;font-weight:600;letter-spacing:1px}
.contact p{font-size:14px;line-height:21px;color:var(--muted);margin-top:24px}
.contact form{display:flex;margin-top:20px;gap:6px}
.contact .field{flex:1;height:44px;background:var(--field);font-size:14px;color:#888;padding:13px 14px;letter-spacing:.5px}
.contact .send{width:108px;height:44px;line-height:44px}
.footer-logo{left:0;width:982px;top:3468px;text-align:center;font-size:28px}
.social{left:431px;top:3528px;display:flex;gap:14px}
.foot-col{top:3601px;font-size:14px;line-height:21px}
.foot-small{font-size:8px;color:var(--muted)}
</style>
</head>
<body>
<div class="page">
  <header>
    <nav class="abs nav">
      <svg width="16" height="12" viewBox="0 0 16 12"><path d="M0 1h16M0 6h16M0 11h16" stroke="#2b2a1e" stroke-width="1.6"/></svg>
      <span>Produkte</span><span>Fertigung</span>
    </nav>
    <div class="abs logo header-logo">VALKORIN</div>
    <div class="abs header-icons">
      <svg width="20" height="20" viewBox="0 0 20 20"><circle cx="8" cy="8" r="6" fill="none" stroke="#2b2a1e" stroke-width="1.6"/><path d="M12.5 12.5l5 5" stroke="#2b2a1e" stroke-width="1.6"/></svg>
      <svg width="20" height="18" viewBox="0 0 20 18"><rect x="1" y="2" width="18" height="14" rx="2" fill="none" stroke="#2b2a1e" stroke-width="1.6"/><path d="M1 4l9 6 9-6" fill="none" stroke="#2b2a1e" stroke-width="1.6"/></svg>
    </div>
  </header>

  <section>
    <div class="abs hero" role="img" aria-label="Foto: Schweißer bei der Arbeit mit Funkenflug"></div>
    <div class="abs hero-kicker">Willkommen bei Valkorin</div>
    <h1 class="abs hero-title">Meisterhafte<br>Metallverarbeitung<br>für Ihre Visionen</h1>
    <div class="abs product-band"></div>
    <div class="abs side-label" style="left:84px;top:672px">Produkte</div>
    <div class="abs product" style="left:121px"><div class="img" role="img" aria-label="Foto: Maschinengestell mit Kälteanlage"></div><h3>Maschinengestelle</h3><p>für spezielle<br>Kälteanlagen</p></div>
    <div class="abs product" style="left:370px"><div class="img" role="img" aria-label="Foto: Spezialgitterbox"></div><h3>Spezialgitterboxen</h3><p>zur Lagerung von<br>Gasen / Flaschen</p></div>
    <div class="abs product" style="left:619px"><div class="img" role="img" aria-label="Foto: Spezialtransportpalette"></div><h3>Spezialtransportpaletten</h3><p>Beispiele für die Lagerung<br>von Gasen / Flaschen</p></div>
    <a class="abs btn" style="left:385px;top:816px;width:210px;height:44px;line-height:44px">Alle Produkte ansehen</a>
  </section>

  <section>
    <div class="abs feat-img" style="left:45px;top:970px;background:linear-gradient(90deg,#4d535d,#98a3b3 40%,#1f3660 75%,#152745)" role="img" aria-label="Foto: Stahlbearbeitung mit Funken und Konstruktionslinien"></div>
    <div class="abs feat-text" style="left:594px;top:1027px"><h2>Stahl- und Palettenbau</h2><p>Wir sind spezialisiert auf die Herstellung von robusten Stahlkonstruktionen und Paletten, die höchsten Ansprüchen gerecht werden.</p><a class="link">Jetzt entdecken</a></div>

    <div class="abs feat-img" style="left:424px;top:1312px;background:linear-gradient(120deg,#1f4a80,#6f92b8 45%,#25446e 80%,#9fb6d0)" role="img" aria-label="Foto: Blechbearbeitungsmaschine"></div>
    <div class="abs feat-text right" style="left:68px;top:1369px"><h2>Blechbearbeitung</h2><p>Unsere Fachleute beherrschen die Kunst der Blechbearbeitung und setzen Ihre Ideen präzise in die Realität um.</p><a class="link">Jetzt entdecken</a></div>

    <div class="abs feat-img" style="left:45px;top:1655px;background:linear-gradient(135deg,#5c7aa3,#3d5c8a 50%,#7c95b8)" role="img" aria-label="Illustration: Edelstahlgestell mit Antrieb"></div>
    <div class="abs feat-text" style="left:594px;top:1712px"><h2>Edelstahlbearbeitung</h2><p>Wir sind spezialisiert auf die Herstellung von robusten Stahlkonstruktionen und Paletten, die höchsten Ansprüchen gerecht werden.</p><a class="link">Jetzt entdecken</a></div>

    <div class="abs feat-img" style="left:424px;top:1997px;background:radial-gradient(circle at 45% 45%,#cfe2f2 0%,#4f7aa5 25%,#1c3a62 70%)" role="img" aria-label="Foto: Mechanische Fertigung in der Werkhalle"></div>
    <div class="abs feat-text right" style="left:68px;top:2054px"><h2>Mechanische Fertigung</h2><p>Präzision ist der Schlüssel zur mechanischen Fertigung, und Präzision ist unsere Stärke.</p><a class="btn" style="margin-top:16px;width:161px;height:44px;line-height:44px;box-shadow:0 3px 8px rgba(0,0,0,.25)">Jetzt entdecken</a></div>
  </section>

  <section>
    <div class="abs reviews"></div>
    <div class="abs side-label" style="left:84px;top:2485px">Reviews</div>
    <div class="abs review" style="left:137px"><div style="color:var(--star);letter-spacing:3px">☆☆☆☆☆</div><h3>Hervorragender Service</h3><p>Die Mitarbeiter sind sehr freundlich und kompetent und konnten uns in diversen Situationen weiterhelfen</p><small>L. Berger,<br>Nordwind Kühlsysteme GmbH</small></div>
    <div class="abs review" style="left:393px"><div style="color:var(--star);letter-spacing:3px">☆☆☆☆☆</div><h3>Reibungsloser Kauf und excellente Qualität</h3><p>Valkorin liefert Qualität. Wir sind sehr zufrieden.</p><small>K. Vogt,<br>Anlagenservice Ost</small></div>
    <div class="abs review" style="left:649px"><div style="color:var(--star);letter-spacing:3px">☆☆☆☆☆</div><h3>Top Service aus Deutschland</h3><p>Die Mitarbeiter sind sehr freundlich und kompetent und konnten uns in diversen Situationen weiterhelfen.</p><small>M. Kranz,<br>Lumeco Lasertechnik</small></div>
  </section>

  <section>
    <h2 class="abs about-title">Über Valkorin</h2>
    <div class="abs about-img" style="left:45px;background:linear-gradient(180deg,#8d8f90,#c9cbc7 50%,#6f716e)" role="img" aria-label="Foto: Lagerhalle mit Regalen"></div>
    <div class="abs about-img" style="left:345px;background:linear-gradient(160deg,#4b4f52,#9a9d9d 50%,#3f4345)" role="img" aria-label="Luftbild: Firmengelände"></div>
    <div class="abs about-img" style="left:645px;background:linear-gradient(135deg,#2c3e5c,#9cb0c8 50%,#3a4f70)" role="img" aria-label="Foto: Stahlgitterkonstruktion"></div>
    <div class="abs about-col" style="left:75px"><h3>Qualität</h3><p>Seit 2001 wachsen wir in Kellbach bei Auenstadt kontinuierlich und leidenschaftlich, um Ihr Experte für hochwertige Metallverarbeitung zu sein.</p></div>
    <div class="abs about-col" style="left:375px"><h3>Geschichte</h3><p>Unser Team aus hochqualifizierten Fachkräften setzt mit Innovationsgeist und Präzision modernste Maschinen ein, um Ihren Anforderungen gerecht zu werden.</p></div>
    <div class="abs about-col" style="left:675px"><h3>Partner</h3><p>Valkorin ist mehr als ein Dienstleister - wir sind Ihr engagierter Partner, der gemeinsam mit Ihnen an der Verwirklichung Ihrer Metallprojekte arbeitet.</p></div>
  </section>

  <section class="abs contact">
    <h2>KONTAKT</h2>
    <p>Kontaktieren Sie uns noch heute, um mehr darüber zu erfahren, wie Valkorin Ihnen helfen kann. Wir freuen uns darauf, Ihr nächstes Metallverarbeitungsprojekt in die Realität umzusetzen – alles made in Germany!</p>
    <form><div class="field">Ihre E-Mailadresse</div><div class="btn send">Absenden</div></form>
  </section>

  <footer>
    <div class="abs logo footer-logo">VALKORIN</div>
    <div class="abs social">
      <svg width="28" height="28" viewBox="0 0 28 28"><circle cx="14" cy="14" r="12.5" fill="none" stroke="#0c3a72" stroke-width="1.6"/><circle cx="14" cy="14" r="4" fill="#0c3a72"/></svg>
      <svg width="28" height="28" viewBox="0 0 28 28"><circle cx="14" cy="14" r="12.5" fill="none" stroke="#0c3a72" stroke-width="1.6"/><circle cx="14" cy="14" r="4" fill="#0c3a72"/></svg>
      <svg width="28" height="28" viewBox="0 0 28 28"><circle cx="14" cy="14" r="12.5" fill="none" stroke="#0c3a72" stroke-width="1.6"/><circle cx="14" cy="14" r="4" fill="#0c3a72"/></svg>
    </div>
    <div class="abs foot-col" style="left:110px">Halden Stahlwerk<br>Lindenweg 12<br>08712 Kellbach<br>Inhaber: Tobias Halden</div>
    <div class="abs foot-col" style="left:322px">Impressum<br>AGB<br>Datenschutz<br>Jobs</div>
    <div class="abs foot-col" style="left:511px;top:3616px"><strong style="font-weight:600">Telefon 03841 / 000 412 7</strong><div class="foot-small" style="line-height:10px">Mo-Fr, 08:30 - 17:30 Uhr</div><div class="foot-small" style="margin-top:18px">© 2023 Valkorin, Deutschland</div></div>
  </footer>
</div>
</body>
</html>
```